Home Remodeling company needs a business card design

we need a business card design for home remodeling company in hamilton county, indiana USA. we offers a wide range of construction services including whole house renovations, Design and Build Basements and Kitchen and Bathroom Remodeling . we would like to see designs for both site of business card that use the same color of the company logo and also including all information below :
1- Karim Feltous CEO / General Contractor
2- all company contacts Telephone numbers ( 1-888-DULOM-47 ) ( 317-555-0193) email address ( info@dulomhome.com) website ( www.dulomhome.com ) and social media logos (Facebook- twitter- google plus )
3- company logo
4- licensed . insured . bonded

```html
<!DOCTYPE html>
<html lang="en">
<head>
<meta charset="utf-8">
<title>Dulom Home Remodeling – Business Card</title>
<link rel="stylesheet" href="https://fonts.googleapis.com/css2?family=Cabin:wght@400;500;700&display=swap">
<style>
  :root {
    --backdrop: #9c9c9c;
    --card: #f3f3f2;
    --ink: #2b2b2b;
    --ink-soft: #3c3c3c;
    --brand-red: #b02a30;
    --rule: #8a8a8a;
  }
  * { box-sizing: border-box; margin: 0; padding: 0; }
  html, body { width: 1105px; height: 1200px; overflow: hidden; }
  body {
    background: var(--backdrop);
    font-family: "Cabin", "Gill Sans", sans-serif;
    color: var(--ink);
    position: relative;
  }
  .card {
    position: absolute;
    left: 180px;
    width: 745px;
    height: 427px;
    background: var(--card);
  }
  .card--front { top: 119px; }
  .card--back { top: 636px; }

  /* Front */
  .brand {
    position: absolute;
    left: 190px;
    top: 98px;
    display: flex;
    align-items: center;
    gap: 16px;
  }
  .brand__mark {
    width: 18px;
    height: 18px;
    background: var(--brand-red);
  }
  .brand__name {
    font-weight: 700;
    font-size: 64px;
    letter-spacing: 4px;
    line-height: 1;
    color: var(--ink);
  }
  .person {
    position: absolute;
    right: 392px;
    top: 252px;
    text-align: right;
  }
  .person__name {
    font-weight: 500;
    font-size: 27px;
    color: var(--ink);
    line-height: 1.15;
  }
  .person__title {
    font-size: 21px;
    color: var(--brand-red);
    margin-top: 4px;
  }
  .divider {
    position: absolute;
    left: 375px;
    top: 224px;
    width: 1px;
    height: 113px;
    background: var(--rule);
  }
  .contacts {
    position: absolute;
    left: 410px;
    top: 228px;
    list-style: none;
  }
  .contacts li {
    display: flex;
    align-items: center;
    gap: 10px;
    height: 29px;
    font-size: 19px;
    color: var(--ink-soft);
  }
  .contacts svg { width: 16px; height: 16px; fill: var(--ink); flex: none; }

  /* Back */
  .back-mark {
    position: absolute;
    left: 332px;
    top: 96px;
    width: 80px;
    height: 80px;
    background: var(--brand-red);
  }
  .back-name {
    position: absolute;
    left: 0; right: 0;
    top: 192px;
    text-align: center;
    font-weight: 700;
    font-size: 26px;
    letter-spacing: 4px;
    color: var(--ink);
  }
  .credentials {
    position: absolute;
    left: 0; right: 0;
    top: 262px;
    text-align: center;
    font-size: 22px;
    color: var(--brand-red);
    letter-spacing: 0.5px;
  }
  .services {
    position: absolute;
    left: 0; right: 0;
    top: 297px;
    text-align: center;
    font-size: 17.5px;
    line-height: 23px;
    color: var(--ink-soft);
  }
  .social {
    position: absolute;
    left: 0; right: 0;
    top: 357px;
    display: flex;
    justify-content: center;
    align-items: center;
    gap: 5px;
  }
  .social__line {
    width: 58px;
    height: 1px;
    background: var(--rule);
    margin: 0 6px;
  }
  .social__dot {
    width: 26px;
    height: 26px;
    border-radius: 50%;
    background: var(--ink);
  }
</style>
</head>
<body>
  <section class="card card--front">
    <div class="brand">
      <span class="brand__mark"></span>
      <span class="brand__name">DULOM</span>
    </div>

    <div class="person">
      <p class="person__name">Karim Feltous</p>
      <p class="person__title">CEO / General Contractor</p>
    </div>

    <div class="divider"></div>

    <ul class="contacts">
      <li>
        <svg viewBox="0 0 16 16" aria-hidden="true"><path d="M3.2 1.2l2.4 2.6-1.3 1.9c.9 2 2.4 3.6 4.4 4.6l1.8-1.4 2.7 2.3-1.4 2.6C6.7 13.6 2.2 9 1.5 3.3z"/></svg>
        1-888-DULOM-47
      </li>
      <li>
        <svg viewBox="0 0 16 16" aria-hidden="true"><path d="M4.5 0.5h7a1 1 0 0 1 1 1v13a1 1 0 0 1-1 1h-7a1 1 0 0 1-1-1v-13a1 1 0 0 1 1-1zm.8 2v9.5h5.4V2.5zM8 12.8a.9.9 0 1 0 0 1.8.9.9 0 0 0 0-1.8z"/></svg>
        317-555-0193
      </li>
      <li>
        <svg viewBox="0 0 16 16" aria-hidden="true"><path d="M1 3.5h14v1L8 9 1 4.5zM1 6l7 4.5L15 6v6.5H1z"/></svg>
        info@dulomhome.com
      </li>
      <li>
        <svg viewBox="0 0 16 16" aria-hidden="true"><circle cx="8" cy="8" r="7"/><path d="M4 5.5c1.5-.5 2.5.5 3 1.5s-.5 2 .5 3 .5 2.5-.5 3.5c-2-.5-3-2-3.5-3.5S3 6.5 4 5.5zm6-3c1 .5 2.5 1.5 3 3-1 .5-2 0-2.5-.8S9.5 3 10 2.5z" fill="#f3f3f2"/></svg>
        www.dulomhome.com
      </li>
    </ul>
  </section>

  <section class="card card--back">
    <div class="back-mark"></div>
    <p class="back-name">DULOM</p>
    <p class="credentials">LICENSED | INSURED | BONDED</p>
    <p class="services">
      Construction services | Whole house renovations<br>
      Design &amp; Build Basements | Kitchen &amp; Bathroom Remodeling
    </p>
    <div class="social" aria-label="Social media">
      <span class="social__line"></span>
      <span class="social__dot"></span>
      <span class="social__dot"></span>
      <span class="social__dot"></span>
      <span class="social__line"></span>
    </div>
  </section>
</body>
</html>
```